To design a brand identity that is simple and creative with 'Corvane' as the brand name, I like modern simple fonts like helvetica neue, I want to print both sides of the card, I am open to dark front and white back, but the design needs to transfer well to letter heads and email signatures, I am looking for sophisticated and elegant, but open minded about clever and off the wall, I do not do 'boring' Corvane Ventures is the mother company for a small group, specialising in Management & consulting, Software development and construction, we have a high level of integrity, we are transparent and accountable for what we do. my images are provided as a guide only, Im not expecting them to be just copied, Im looking for a creator and passionate thinker, who will put life into their work.

Target Market(s)

usually business minded people who are looking for something different in me, such as leadership, confidence and focus with thinking that is per haps a little outside the box..

Industry/Entity Type

Construction

Requirements
Must have
• clean, minmalistic
Nice to have
• custom logo
Should not have
• boring, traditional

```html
<!DOCTYPE html>
<html lang="en">
<head>
<meta charset="utf-8">
<title>Corvane Ventures – Business Card</title>
<link rel="stylesheet" href="https://fonts.googleapis.com/css2?family=Poppins:wght@300;400&family=Inter:wght@400&family=Dancing+Script:wght@400&display=swap">
<style>
  :root {
    --stage: #2f2c2a;
    --card-light: #ffffff;
    --card-dark: #2b2a2a;
    --card-dark-edge: #1e1d1d;
    --ink: #1c1c1c;
    --ink-soft: #555555;
    --accent: #e2362d;
    --accent-warm: #e8663a;
    --paper-pattern-a: #fbfbfb;
    --paper-pattern-b: #ececec;
    --photo-top: #f4f3f2;
    --photo-mid: #d9d6d4;
    --photo-low: #efefef;
    --light-text: #f2f2f2;
    --caption: #d8d8d8;
  }
  * { box-sizing: border-box; margin: 0; padding: 0; }
  html, body { width: 1200px; height: 1000px; overflow: hidden; }
  body { background: var(--stage); position: relative; font-family: "Inter", Helvetica, Arial, sans-serif; }

  .card { position: absolute; }

  /* Front card */
  .card-front {
    left: 140px; top: 130px; width: 420px; height: 720px;
    background: var(--card-light);
    overflow: hidden;
  }
  .front-pattern {
    position: absolute; inset: 0;
    background: linear-gradient(160deg, var(--paper-pattern-a) 0%, var(--paper-pattern-b) 55%, var(--paper-pattern-a) 100%);
  }
  .front-photo {
    position: absolute; left: 0; right: 0; bottom: 0; height: 330px;
    background: linear-gradient(180deg, rgba(244,243,242,0) 0%, var(--photo-mid) 40%, var(--photo-mid) 72%, var(--photo-low) 100%);
  }
  .brand-lockup {
    position: absolute; top: 70px; right: 48px;
    display: flex; align-items: center; gap: 16px;
  }
  .brand-mark { width: 58px; height: 58px; border-radius: 50%; background: var(--accent-warm); }
  .brand-name {
    font-family: "Poppins", Helvetica, Arial, sans-serif; font-weight: 300;
    font-size: 58px; line-height: 1; color: var(--ink); letter-spacing: 0.5px;
  }
  .tagline {
    position: absolute; top: 142px; right: 48px;
    font-family: "Dancing Script", cursive; font-size: 22px; color: var(--ink);
  }
  .web-address {
    position: absolute; top: 172px; right: 48px;
    font-family: "Poppins", Helvetica, Arial, sans-serif; font-weight: 300;
    font-size: 20px; color: var(--ink-soft);
  }
  .web-address .web-prefix { color: var(--accent-warm); }
  .motto {
    position: absolute; top: 232px; right: 60px;
    font-family: "Dancing Script", cursive; font-size: 32px; color: var(--ink);
  }
  .contact-block {
    position: absolute; right: 40px; top: 500px; text-align: right; color: var(--ink);
  }
  .contact-name {
    font-family: "Poppins", Helvetica, Arial, sans-serif; font-weight: 400;
    font-size: 34px; margin-bottom: 14px;
  }
  .contact-line {
    display: flex; align-items: center; justify-content: flex-end; gap: 8px;
    font-size: 16px; margin-bottom: 10px;
  }
  .contact-icon { width: 18px; height: 18px; flex: none; }

  /* Back card */
  .card-back {
    left: 600px; top: 320px; width: 560px; height: 340px;
    background: radial-gradient(ellipse at 45% 35%, #3d3c3c 0%, var(--card-dark) 55%, var(--card-dark-edge) 100%);
  }
  .back-lockup {
    position: absolute; left: 40px; top: 110px;
    display: flex; align-items: center; gap: 22px;
  }
  .back-lockup .brand-mark { width: 96px; height: 96px; }
  .back-lockup .brand-name { color: var(--light-text); font-size: 92px; }
  .services {
    position: absolute; left: 60px; top: 232px;
    font-family: "Poppins", Helvetica, Arial, sans-serif; font-weight: 300;
    font-size: 17px; letter-spacing: 2px; color: var(--light-text);
    display: flex; align-items: center; gap: 12px;
  }
  .service-dot { width: 6px; height: 6px; background: var(--accent); border-radius: 50%; }

  .caption {
    position: absolute; font-size: 20px; color: var(--caption);
    font-family: "Inter", Helvetica, Arial, sans-serif;
  }
  .caption-front { left: 140px; top: 870px; }
  .caption-back { left: 1100px; top: 680px; }
</style>
</head>
<body>

<section class="card card-front" aria-label="Front of business card">
  <div class="front-pattern" role="img" aria-label="Soft white embossed cube pattern background"></div>
  <div class="front-photo" role="img" aria-label="Monochrome photograph of a glacier wall with a small boat on icy water"></div>

  <div class="brand-lockup">
    <span class="brand-mark"></span>
    <span class="brand-name">corvane</span>
  </div>
  <p class="tagline">... in the creation business</p>
  <p class="web-address"><span class="web-prefix">www.</span> corvane.ventures</p>
  <p class="motto">‘pure passion’</p>

  <div class="contact-block">
    <p class="contact-name">marcus</p>
    <p class="contact-line">+ 61 0400 555 214
      <svg class="contact-icon" viewBox="0 0 24 24" aria-hidden="true"><path fill="#e2362d" d="M6.6 10.8a15.1 15.1 0 0 0 6.6 6.6l2.2-2.2c.3-.3.7-.4 1-.2 1.1.4 2.3.6 3.6.6.6 0 1 .4 1 1V20c0 .6-.4 1-1 1A17 17 0 0 1 3 4c0-.6.4-1 1-1h3.5c.6 0 1 .4 1 1 0 1.3.2 2.5.6 3.6.1.3 0 .7-.2 1z"/></svg>
    </p>
    <p class="contact-line">marcus@corvane.ventures
      <svg class="contact-icon" viewBox="0 0 24 24" aria-hidden="true"><rect x="2" y="5" width="20" height="14" fill="#e2362d"/><path d="M2 5l10 8 10-8" fill="none" stroke="#ffffff" stroke-width="1.6"/></svg>
    </p>
  </div>
</section>

<section class="card card-back" aria-label="Back of business card">
  <div class="back-lockup">
    <span class="brand-mark"></span>
    <span class="brand-name">corvane</span>
  </div>
  <p class="services">
    <span>management</span><span class="service-dot"></span>
    <span>software</span><span class="service-dot"></span>
    <span>construction</span>
  </p>
</section>

<p class="caption caption-front">Front</p>
<p class="caption caption-back">Back</p>

</body>
</html>
```